Velmora Consulting Business

** Please add the content information from my old business card
1. I would like to see a two sided business card with both options with the 1st Option--Tallow Spire-new WHITE BACKGROUND LOGO
2 nd Option-Tallow Spire - new BLACK- Background Logo
3rd -Option a business card with my Photo on the card
Please add the new word to the card information:
EXECUTION
AS THE OWNER'S REP
WE AIM TO ACHIEVE YOUR
INFRASTRUCTURE VISION with
OUR SPECIALIZATION & EXECUTION in:

FUNDING Planning
BUSINESS Planning
INFRASTRUCTURE Planning
PROJECT Management
Since 2012
_____________________________________________________________________
I want to get spot uv raised printing. I was liking a a nice rich white linen paper stock with black writing & NOT A COLORED CARD other than a variety of white or black cards concept

```html
<!DOCTYPE html>
<html lang="en">
<head>
<meta charset="utf-8">
<title>Velmora Consulting – Business Card</title>
<link href="https://fonts.googleapis.com/css2?family=Montserrat:wght@400;500;700;800&display=swap" rel="stylesheet">
<style>
  :root {
    --stage: #1f1f20;
    --card: #ffffff;
    --ink: #1b1b1b;
    --accent: #e3192f;
  }
  * { box-sizing: border-box; margin: 0; padding: 0; }
  html, body {
    width: 1200px; height: 900px; overflow: hidden;
    background: var(--stage);
    font-family: "Montserrat", Arial, sans-serif;
    color: var(--ink);
  }
  .card {
    position: absolute; left: 240px;
    width: 720px; height: 400px;
    background: var(--card);
    border-radius: 26px;
    overflow: hidden;
  }
  .card--front { top: 30px; }
  .card--back  { top: 470px; }

  .brand {
    position: absolute; left: 40px; top: 0; bottom: 0;
    width: 240px;
    display: flex; flex-direction: column; justify-content: center; align-items: flex-start;
    gap: 4px;
  }
  .brand__row { display: flex; align-items: center; gap: 12px; }
  .brand__mark { width: 26px; height: 26px; background: var(--ink); }
  .brand__name, .brand__sub { font-weight: 700; color: var(--ink); line-height: 1; }
  .brand__name { font-size: 46px; letter-spacing: -1px; }
  .brand__sub { font-size: 14px; letter-spacing: 8px; padding-left: 38px; }

  .divider {
    position: absolute; left: 300px; top: 70px; bottom: 70px;
    width: 2px; background: var(--accent);
  }

  .pitch { position: absolute; left: 326px; top: 66px; right: 30px; }
  .pitch__lead {
    color: var(--accent); font-weight: 800; font-size: 14px;
    line-height: 1.35; text-transform: uppercase; margin-bottom: 20px;
  }
  .pitch__list { list-style: none; font-size: 16px; font-weight: 500; line-height: 1.65; }

  .contact { position: absolute; left: 326px; top: 66px; right: 20px; }
  .contact__name {
    color: var(--accent); font-weight: 800; font-size: 25px; line-height: 1.15;
    white-space: nowrap;
  }
  .contact__role { font-size: 16px; font-weight: 500; margin-top: 10px; }
  .contact__place { font-size: 16px; font-weight: 500; margin-top: 10px; }
  .contact__lines { list-style: none; margin-top: 18px; font-size: 16px; font-weight: 500; }
  .contact__lines li { display: flex; align-items: center; gap: 12px; line-height: 1.75; }
  .contact__lines svg { width: 16px; height: 16px; flex: none; }

  .edge-band { position: absolute; left: 0; right: 0; bottom: 0; height: 14px; }
</style>
</head>
<body>

<section class="card card--front" aria-label="Card front">
  <div class="brand">
    <div class="brand__row"><span class="brand__mark"></span><span class="brand__name">Velmora</span></div>
    <span class="brand__sub">CONSULTING</span>
  </div>
  <div class="divider"></div>
  <div class="pitch">
    <p class="pitch__lead">As the owner's rep<br>we aim to achieve your<br>infrastructure vision with<br>our specialization &amp; execution in:</p>
    <ul class="pitch__list">
      <li>FUNDING Planning</li>
      <li>BUSINESS Planning</li>
      <li>INFRASTRUCTURE Planning</li>
      <li>PROJECT Management</li>
      <li>Since 2012</li>
    </ul>
  </div>
</section>

<section class="card card--back" aria-label="Card back">
  <div class="brand">
    <div class="brand__row"><span class="brand__mark"></span><span class="brand__name">Velmora</span></div>
    <span class="brand__sub">CONSULTING</span>
  </div>
  <div class="divider"></div>
  <div class="contact">
    <h1 class="contact__name">Marisol Tenbrook-Adair</h1>
    <p class="contact__role">CEO / LEAD PROJECT MANAGER</p>
    <p class="contact__place">Northgate NT · Riverton NB</p>
    <ul class="contact__lines">
      <li>
        <svg viewBox="0 0 16 16" aria-hidden="true"><path fill="var(--accent)" d="M3.6 1.5 6 4.2 4.7 5.8c.9 2 2.5 3.6 4.5 4.5l1.6-1.3 2.7 2.4-1.3 2.3C7.2 13.5 2.5 8.8 1.3 3z"/></svg>
        <span>555.014.2290</span>
      </li>
      <li>
        <svg viewBox="0 0 16 16" aria-hidden="true"><rect x="1" y="3" width="14" height="10" rx="1" fill="var(--accent)"/><path d="M1.5 3.8 8 9l6.5-5.2" stroke="#fff" stroke-width="1.3" fill="none"/></svg>
        <span>mari@velmora.ca</span>
      </li>
      <li>
        <svg viewBox="0 0 16 16" aria-hidden="true"><circle cx="8" cy="8" r="6.5" fill="var(--accent)"/><path d="M1.5 8h13M8 1.5c-3 3.5-3 9.5 0 13M8 1.5c3 3.5 3 9.5 0 13" stroke="#fff" stroke-width="1" fill="none"/></svg>
        <span>www.velmora.ca</span>
      </li>
    </ul>
  </div>
  <svg class="edge-band" viewBox="0 0 720 14" preserveAspectRatio="none" aria-hidden="true">
    <polygon points="0,0 330,0 322,14 0,14" fill="var(--ink)"/>
    <polygon points="340,0 720,0 720,14 332,14" fill="var(--accent)"/>
  </svg>
</section>

</body>
</html>
```